All-Natural Head Lice Removal company

I need a business card with my pre-existing logo. We are a new company located in Portland Oregon that goes into peoples homes to help with head lice removal. My products and approach are all- natural and also will be around children.On my current logo we used Teal Bl and the color Green. I am open to new ideas just want it simple and creative

Target Market(s)

my biggest market is families of school aged children

Industry/Entity Type

Business

Contact Information for Business Card

see upload for details from previous business card

Font styles to use
Serif

Colors
33a6d7
9bcb3b
f37122

Requirements
Must have
• Basic information/ logo put into a creative format that is catching to the eye
Nice to have
• creative

```html
<!DOCTYPE html>
<html lang="en">
<head>
<meta charset="utf-8">
<title>NitPick Home – Business Card</title>
<link href="https://fonts.googleapis.com/css2?family=Arvo:wght@400;700&display=swap" rel="stylesheet">
<style>
  :root {
    --sky-top: #86d6f4;
    --sky-bottom: #2f97d4;
    --ink: #111214;
    --ink-soft: #2b2b2b;
    --leaf: #8cc63f;
    --paper: #ffffff;
    --stage: #e9ecef;
  }
  * { box-sizing: border-box; margin: 0; padding: 0; }
  html, body {
    width: 1200px; height: 913px; overflow: hidden;
    background: var(--stage);
    font-family: "Arvo", Georgia, serif;
  }
  .stage {
    position: relative; width: 1200px; height: 913px;
    display: flex; align-items: center; justify-content: center; gap: 60px;
  }
  .card {
    position: relative; width: 520px; height: 297px; overflow: hidden;
    background: linear-gradient(180deg, var(--sky-top), var(--sky-bottom));
    box-shadow: 0 6px 18px rgba(0,0,0,.18);
  }
  .card-curve { position: absolute; inset: 0; width: 100%; height: 100%; }

  .brand { display: flex; align-items: center; gap: 10px; }
  .brand-dot { width: 34px; height: 34px; border-radius: 50%; background: var(--leaf); }
  .brand-name { font-weight: 700; color: var(--ink-soft); font-size: 26px; line-height: 1; }

  /* front */
  .front .brand { position: absolute; left: 330px; top: 70px; }
  .front .brand-name { font-size: 22px; }
  .front .tagline {
    position: absolute; left: 330px; top: 128px;
    font-size: 13px; line-height: 1.35; color: var(--ink-soft);
  }
  .person { position: absolute; left: 30px; top: 92px; }
  .person-name { color: var(--leaf); font-size: 20px; letter-spacing: .5px; text-transform: uppercase; }
  .person-role { color: var(--paper); font-size: 12px; text-transform: uppercase; margin-top: 2px; }
  .contacts { position: absolute; left: 30px; top: 196px; list-style: none; }
  .contacts li {
    display: flex; align-items: center; gap: 8px;
    color: var(--leaf); font-size: 13px; line-height: 1.55;
  }
  .contacts svg { width: 11px; height: 11px; flex: none; }

  /* back */
  .back { display: flex; flex-direction: column; align-items: center; justify-content: center; text-align: center; }
  .back .brand { margin-bottom: 34px; }
  .back .brand-dot { width: 52px; height: 52px; }
  .back .brand-name { font-size: 36px; }
  .back .slogan { font-size: 14px; font-weight: 700; color: var(--ink-soft); line-height: 1.35; }
  .back .web { font-size: 12px; color: var(--paper); margin-top: 8px; }
</style>
</head>
<body>
<main class="stage">

  <section class="card front">
    <svg class="card-curve" viewBox="0 0 520 297" preserveAspectRatio="none" aria-hidden="true">
      <path d="M0 0 H215 C310 70 330 200 262 297 H0 Z" fill="var(--ink)"/>
      <path d="M222 0 C318 70 338 200 270 297" fill="none" stroke="var(--paper)" stroke-width="4"/>
    </svg>

    <div class="person">
      <p class="person-name">Dana Whitfield</p>
      <p class="person-role">Owner</p>
    </div>

    <ul class="contacts">
      <li>
        <svg viewBox="0 0 12 12"><path d="M3 1 L5 3 L4 5 Q5 7 7 8 L9 7 L11 9 L9.5 11 Q4 10 1 3 Z" fill="var(--paper)"/></svg>
        1-855-555-NITS (6487)
      </li>
      <li>
        <svg viewBox="0 0 12 12"><rect x="1" y="2.5" width="10" height="7" fill="none" stroke="var(--paper)"/><path d="M1 2.5 L6 7 L11 2.5" fill="none" stroke="var(--paper)"/></svg>
        dana@nitpickhome.com
      </li>
      <li>
        <svg viewBox="0 0 12 12"><circle cx="6" cy="6" r="5" fill="none" stroke="var(--paper)"/><path d="M1 6 H11 M6 1 Q2.5 6 6 11 M6 1 Q9.5 6 6 11" fill="none" stroke="var(--paper)"/></svg>
        www.nitpickhome.com
      </li>
    </ul>

    <div class="brand">
      <span class="brand-dot"></span>
      <span class="brand-name">NitPick Home</span>
    </div>
    <p class="tagline">All Natural In-Home<br>Lice Removal Services</p>
  </section>

  <section class="card back">
    <div class="brand">
      <span class="brand-dot"></span>
      <span class="brand-name">NitPick Home</span>
    </div>
    <p class="slogan">Try NitPick Home Today and Be Lice Free Tomorrow!<br>All Natural In-Home Lice Removal Services</p>
    <p class="web">www.nitpickhome.com</p>
  </section>

</main>
</body>
</html>
```